Business Card - high end, modern health care

Hey designers!

We need a double sided business card for the boutique, cutting edge physical therapy rehabilitation centre in Sydney's Northern Beaches.

With the most qualified physios in the area The Harbourview Motion Clinic does what other physiotherapy practices do not, we take our time with our patients giving them longer appointments, better physios and therefor faster results!

We guarantee that the service people receive at THMC will be unparalleled.

Hence we need a business card to reflect our modern, boutique, high end service. The final design needs to reflect that we are in a class of our own yet with the feel of beachside retreat.

Below I have attached our logo in both blue on white and white on blue. The exact colour is;
and the font that we have used in our logo is Tex Gyre Aventador.

I like the idea of the blue as the main colour as it is more eye catching and our signage onto the main road will be in this blue and in the interest of consistency across marketing the blue needs to be a part of the design. However I would appreciate a few designs onto a wooden background as this is a visual theme within the fitout of the practice.

The design needs to be of standard size (91x55mm).

Target Market(s)

We target people who have an end outcome in mind and those who have had poor experiences with other providers and ensure that everyone gets the care that they deserve with a premium service that is tailored to the individuals circumstances. As a premium service, the target market is highly educated, business and tech savvy with the additional target market of elderly people who have self funded their retirement and see value in paying for the best ongoing rehabilitation to maintain independence.

Industry/Entity Type

Physical Therapy

Contact Information for Business Card

Name, designation( Titled Musculoskeletal Physiotherapist... there will also be those in the company that have multiple designations ie 5 or 6 words long), phone number, email, facebook, instagram, address

Font styles to use
Sans Serif

Colors

Designer to choose colors to be used in the design.

Requirements
Must have
• Front - The logo as large as possible, blue or wooden theme, and all of the important details.
• Back - A blank space/lines on which to write appointment times (no "Appointment, date, time" etc.)
Nice to have
• facebook url
• logos for facebook and instagram
• Mini logos for the phone and email?

```html
<!DOCTYPE html>
<html lang="en">
<head>
<meta charset="utf-8">
<title>The Harbourview Motion Clinic — Business Card</title>
<link href="https://fonts.googleapis.com/css2?family=Montserrat:wght@400;500;600;700&family=Great+Vibes&display=swap" rel="stylesheet">
<style>
  :root {
    --brand-blue: #0f56a8;
    --brand-blue-deep: #0b4a93;
    --bg-blue-light: #0f5aa6;
    --bg-blue-dark: #0a3f80;
    --card-white: #ffffff;
    --card-grey: #e4e6ea;
    --text-blue: #0f4f9c;
    --line-grey: #b9bec6;
    --label-grey: #7d838c;
  }
  * { margin: 0; padding: 0; box-sizing: border-box; }
  html, body { width: 800px; height: 1200px; overflow: hidden; }
  body {
    position: relative;
    background: radial-gradient(ellipse at 50% 45%, var(--bg-blue-light) 0%, var(--bg-blue-dark) 85%);
    font-family: "Montserrat", sans-serif;
    color: var(--text-blue);
  }
  .card {
    position: absolute;
    top: 464px;
    width: 357px;
    height: 196px;
    border-radius: 14px;
    overflow: hidden;
    background: linear-gradient(135deg, var(--card-white) 0%, var(--card-white) 45%, var(--card-grey) 100%);
    box-shadow: 0 6px 10px rgba(0, 0, 0, 0.35);
  }
  .card::after {
    content: "";
    position: absolute;
    left: 0; right: 0; bottom: 0;
    height: 6px;
    background: var(--brand-blue);
  }
  .card--front { left: 29px; }
  .card--back { left: 410px; }

  .wordmark {
    position: absolute;
    display: flex;
    align-items: center;
    gap: 6px;
    font-weight: 600;
    color: var(--text-blue);
  }
  .wordmark__mark {
    flex: none;
    border-radius: 50%;
    background: var(--text-blue);
  }
  .wordmark__text { line-height: 1; }
  .wordmark__line1 { display: block; letter-spacing: 0.2px; }
  .wordmark__line2 { display: block; letter-spacing: 2.6px; margin-top: 2px; }

  .card--front .wordmark { left: 22px; top: 30px; }
  .card--front .wordmark__mark { width: 30px; height: 30px; }
  .card--front .wordmark__line1 { font-size: 14.5px; }
  .card--front .wordmark__line2 { font-size: 10px; }

  .deco-disc { position: absolute; }
  .card--front .deco-disc { right: -8px; top: -6px; width: 132px; height: 200px; }
  .card--back .deco-disc { left: 0; top: 0; width: 105px; height: 196px; }

  .holder {
    position: absolute;
    left: 22px; top: 125px;
    width: 244px;
    padding-bottom: 4px;
    border-bottom: 1px solid var(--text-blue);
    font-size: 9.5px;
    white-space: nowrap;
  }
  .holder__name { font-weight: 700; }
  .holder__role { font-weight: 400; font-size: 8px; }

  .contact {
    position: absolute;
    left: 22px;
    display: flex;
    align-items: center;
    gap: 5px;
    font-size: 7px;
    white-space: nowrap;
  }
  .contact--phone { top: 153px; }
  .contact--email { top: 153px; left: 108px; }
  .contact--social { top: 170px; }
  .icon { width: 9px; height: 9px; flex: none; }
  .social-dots { display: flex; align-items: center; gap: 2px; font-size: 7px; }
  .social-dot { width: 8px; height: 8px; border-radius: 50%; background: var(--text-blue); }

  .card--back .wordmark { left: 128px; top: 60px; }
  .card--back .wordmark__mark { width: 32px; height: 32px; }
  .card--back .wordmark__line1 { font-size: 15.5px; }
  .card--back .wordmark__line2 { font-size: 10.5px; }

  .appointment-box {
    position: absolute;
    left: 131px; top: 104px;
    width: 192px; height: 37px;
    border: 1px solid var(--line-grey);
    border-radius: 5px;
  }
  .appointment-box__title {
    position: absolute;
    left: 50%; top: -9px;
    transform: translateX(-50%);
    padding: 0 5px;
    background: #f1f2f4;
    font-family: "Great Vibes", cursive;
    font-size: 11px;
    color: var(--label-grey);
  }
  .field {
    position: absolute;
    display: flex;
    align-items: flex-end;
    gap: 2px;
    font-size: 5.8px;
    color: var(--label-grey);
  }
  .field__line { flex: 1; border-bottom: 1px solid var(--line-grey); height: 5px; }
  .field--name { left: 17px; top: 12px; width: 158px; }
  .field--date { left: 17px; top: 22px; width: 78px; }
  .field--time { left: 98px; top: 22px; width: 77px; }

  .wordmark--hero { left: 246px; top: 762px; gap: 9px; color: var(--card-white); }
  .wordmark--hero .wordmark__mark { width: 54px; height: 54px; background: var(--card-white); }
  .wordmark--hero .wordmark__line1 { font-size: 27px; }
  .wordmark--hero .wordmark__line2 { font-size: 17.5px; letter-spacing: 4.6px; margin-top: 4px; }
</style>
</head>
<body>

  <section class="card card--front" aria-label="Card front">
    <div class="wordmark">
      <span class="wordmark__mark"></span>
      <span class="wordmark__text">
        <span class="wordmark__line1">THE HARBOURVIEW</span>
        <span class="wordmark__line2">MOTION CLINIC</span>
      </span>
    </div>

    <svg class="deco-disc" viewBox="0 0 132 200" role="img" aria-label="Large brand emblem area in blue">
      <defs>
        <linearGradient id="frontDisc" x1="0" y1="0" x2="0" y2="1">
          <stop offset="0" stop-color="#1a73c4"/>
          <stop offset="1" stop-color="#0b4a93"/>
        </linearGradient>
      </defs>
      <circle cx="96" cy="100" r="84" fill="url(#frontDisc)"/>
    </svg>

    <p class="holder">
      <span class="holder__name">DANIEL BROOKS</span><span class="holder__role"> / Senior Physiotherapist</span>
    </p>

    <p class="contact contact--phone">
      <svg class="icon" viewBox="0 0 10 10" aria-hidden="true"><circle cx="5" cy="5" r="5" fill="#0f4f9c"/><path d="M3 2.6h1.1l.5 1.3-.7.5a3.6 3.6 0 0 0 1.7 1.7l.5-.7 1.3.5V7c0 .4-.3.5-.6.5A4.6 4.6 0 0 1 2.5 3.2c0-.3.1-.6.5-.6z" fill="#fff"/></svg>
      0061 400 123
    </p>
    <p class="contact contact--email">
      <svg class="icon" viewBox="0 0 10 10" aria-hidden="true"><circle cx="5" cy="5" r="5" fill="#0f4f9c"/><rect x="2.4" y="3.2" width="5.2" height="3.6" fill="#fff"/><path d="M2.4 3.2 5 5.2l2.6-2" fill="none" stroke="#0f4f9c" stroke-width=".6"/></svg>
      contact@harbourviewmotion.com.au
    </p>
    <p class="contact contact--social">
      <span class="social-dots"><span class="social-dot"></span>/<span class="social-dot"></span></span>
      theharbourviewmotion
    </p>
  </section>

  <section class="card card--back" aria-label="Card back">
    <svg class="deco-disc" viewBox="0 0 105 196" role="img" aria-label="Fern frond illustration inside a blue half circle">
      <defs>
        <linearGradient id="backDisc" x1="0" y1="0" x2="1" y2="1">
          <stop offset="0" stop-color="#1a6fc0"/>
          <stop offset="1" stop-color="#0b4a93"/>
        </linearGradient>
      </defs>
      <circle cx="8" cy="98" r="96" fill="url(#backDisc)"/>
    </svg>

    <div class="wordmark">
      <span class="wordmark__mark"></span>
      <span class="wordmark__text">
        <span class="wordmark__line1">THE HARBOURVIEW</span>
        <span class="wordmark__line2">MOTION CLINIC</span>
      </span>
    </div>

    <div class="appointment-box">
      <span class="appointment-box__title">Appointment</span>
      <div class="field field--name">Name:<span class="field__line"></span></div>
      <div class="field field--date">Date:<span class="field__line"></span></div>
      <div class="field field--time">Time:<span class="field__line"></span></div>
    </div>
  </section>

  <div class="wordmark wordmark--hero">
    <span class="wordmark__mark"></span>
    <span class="wordmark__text">
      <span class="wordmark__line1">THE HARBOURVIEW</span>
      <span class="wordmark__line2">MOTION CLINIC</span>
    </span>
  </div>

</body>
</html>
```